Single-sided business card for restaurant velmora with new logo made on this site

Business card options with new logo including restaurant name, address, phone number and website. This business card is single-sided only and will be presented at the hostess desk for clients to take. I would like to see options based on a cream card background, a white card background, a yellow card background and a burgundy colored background. It needs to be elegant and traditional.

Target Market(s)

local and international crowd

Industry/Entity Type

restaurant

Contact Information for Business Card

address, website and phone number

Font styles to use
Serif

Colors
EE7325
F08F49
F5BC92
FAE3D3
FDF4ED

Requirements
Must have
• new logo, address, phone number, website
Should not have
• more than three colors

```html
<!DOCTYPE html>
<html lang="es">
<head>
<meta charset="utf-8">
<title>Velmora – Tarjeta de presentación</title>
<link rel="stylesheet" href="https://fonts.googleapis.com/css2?family=Cinzel:wght@500&family=Cormorant+Garamond:wght@500&family=Arimo:wght@400&display=swap">
<style>
  :root {
    --backdrop: #2b2b2c;
    --burgundy: #3f1d1e;
    --gold: #f5b22a;
    --ink-light: #ffffff;
  }
  * { margin: 0; padding: 0; box-sizing: border-box; }
  html, body {
    width: 1200px;
    height: 1015px;
    overflow: hidden;
    background: var(--backdrop);
  }
  .business-card {
    position: absolute;
    left: 150px;
    top: 250px;
    width: 900px;
    height: 514px;
    background: var(--burgundy);
    overflow: hidden;
  }
  .bottom-band {
    position: absolute;
    left: 0; right: 0; bottom: 0;
    height: 16px;
    background: var(--gold);
  }
  .gold-rule {
    height: 2px;
    background: linear-gradient(90deg, transparent, var(--gold) 20%, var(--gold) 80%, transparent);
  }

  /* Business name */
  .business-name {
    position: absolute;
    left: 118px;
    top: 232px;
    font-family: "Cinzel", serif;
    font-weight: 500;
    font-size: 40px;
    letter-spacing: 2px;
    color: var(--ink-light);
    line-height: 1;
  }

  /* Address */
  .address {
    position: absolute;
    left: 118px;
    top: 320px;
    font-family: "Arimo", sans-serif;
    font-style: normal;
    font-size: 27px;
    line-height: 32px;
    color: var(--ink-light);
  }

  /* Reservations block */
  .contact {
    position: absolute;
    right: 60px;
    top: 60px;
    width: 380px;
    text-align: right;
  }
  .contact-label {
    font-family: "Cinzel", serif;
    font-weight: 500;
    font-size: 26px;
    letter-spacing: 2px;
    color: var(--ink-light);
    line-height: 1;
  }
  .contact-phone {
    font-family: "Cormorant Garamond", serif;
    font-weight: 500;
    font-size: 52px;
    color: var(--ink-light);
    line-height: 1.05;
    margin-top: 2px;
  }
  .contact .gold-rule { width: 300px; margin: 10px 0 18px auto; }
  .contact-web {
    font-family: "Arimo", sans-serif;
    font-size: 22px;
    color: var(--ink-light);
  }
  .contact .gold-rule.lower { margin: 14px 0 0 auto; }
</style>
</head>
<body>
  <div class="business-card">
    <div class="business-name">Velmora</div>

    <address class="address">
      Restaurant Velmora<br>
      Jacaranda 415<br>
      Bahías de Coralina<br>
      Oaxaca CP 70412
    </address>

    <div class="contact">
      <div class="contact-label">RESERVACIONES</div>
      <div class="contact-phone">958-555-0142</div>
      <div class="gold-rule"></div>
      <div class="contact-web">www.velmora.com.mx</div>
      <div class="gold-rule lower"></div>
    </div>

    <div class="bottom-band"></div>
  </div>
</body>
</html>
```